Oil and Gas Exploration and Production company needs a business card design

We need a business card design using our logo and colors in the logo. We want a mainstream design.

```html
<!DOCTYPE html>
<html lang="en">
<head>
<meta charset="utf-8">
<title>Sunward Oil &amp; Gas — Business Card</title>
<link rel="stylesheet" href="https://fonts.googleapis.com/css2?family=Arvo:wght@700&family=Roboto:wght@400&display=swap">
<style>
  :root {
    --bg: #d9d4cc;
    --card-white: #f3f3f2;
    --gold: #c7982f;
    --gold-faint: rgba(199, 152, 47, 0.13);
    --ink: #1c1a17;
    --text: #4a4a4a;
    --white: #ffffff;
  }
  * { margin: 0; padding: 0; box-sizing: border-box; }
  html, body {
    width: 1200px; height: 960px; overflow: hidden;
    background: var(--bg);
  }
  .card {
    position: absolute;
    width: 600px; height: 343px;
    overflow: hidden;
    box-shadow: 0 3px 6px rgba(0,0,0,0.35);
  }
  .card--front { left: 314px; top: 113px; background: var(--card-white); }
  .card--back  { left: 311px; top: 472px; background: var(--gold); }

  .front__decor {
    position: absolute; left: 300px; top: 30px;
    width: 330px; height: 330px; border-radius: 50%;
    border: 58px solid var(--gold-faint);
  }

  .brand {
    position: absolute; left: 38px; top: 42px;
    display: flex; align-items: center; gap: 12px;
  }
  .brand__dot {
    width: 30px; height: 30px; border-radius: 50%;
    background: var(--gold);
  }
  .brand__name {
    font-family: "Arvo", serif; font-weight: 700;
    font-size: 36px; line-height: 1.05; color: var(--ink);
  }

  .contact {
    position: absolute; left: 38px; top: 171px;
    font-family: "Roboto", sans-serif; font-size: 14px;
    color: var(--text); line-height: 19px;
  }
  .contact__address { margin-bottom: 11px; }
  .contact__list { list-style: none; }
  .contact__item { display: flex; align-items: center; gap: 9px; }
  .contact__icon { width: 13px; height: 13px; fill: var(--ink); flex: none; }

  .person {
    position: absolute; right: 36px; top: 221px; text-align: right;
    font-family: "Arvo", serif; font-weight: 700;
  }
  .person__name { font-size: 19px; color: var(--ink); letter-spacing: 0.5px; }
  .person__title { font-size: 13px; color: var(--gold); margin-top: 1px; }

  .back__mark {
    position: absolute; left: 0; right: 0; top: 78px;
    display: flex; flex-direction: column; align-items: center; gap: 22px;
  }
  .back__circle {
    width: 120px; height: 120px; border-radius: 50%;
    background: var(--ink);
  }
  .back__name {
    font-family: "Arvo", serif; font-weight: 700;
    font-size: 30px; color: var(--ink);
  }
  .back__web {
    position: absolute; left: 0; right: 0; top: 287px; text-align: center;
    font-family: "Roboto", sans-serif; font-size: 14px;
    letter-spacing: 4.5px; color: var(--white);
  }
</style>
</head>
<body>
  <section class="card card--front">
    <div class="front__decor"></div>

    <div class="brand">
      <span class="brand__dot"></span>
      <div class="brand__name">Sunward<br>Oil &amp; Gas</div>
    </div>

    <div class="contact">
      <p class="contact__address">2140 Birchwood Road<br>Fairbanks, Alaska 99701</p>
      <ul class="contact__list">
        <li class="contact__item">
          <svg class="contact__icon" viewBox="0 0 16 16"><path d="M3.6 1 6 3.6 4.7 5.6c.9 2.1 3.4 4.7 5.7 5.7l2-1.3L15 12.4l-1.6 2.4C7.8 15 1 8.2 1.2 2.6z"/></svg>
          907 555 0142
        </li>
        <li class="contact__item">
          <svg class="contact__icon" viewBox="0 0 16 16"><path d="M4 0h8a1 1 0 0 1 1 1v14a1 1 0 0 1-1 1H4a1 1 0 0 1-1-1V1a1 1 0 0 1 1-1zm1 2v10h6V2zm3 11a1 1 0 1 0 0 2 1 1 0 0 0 0-2z"/></svg>
          907 555 0187
        </li>
        <li class="contact__item">
          <svg class="contact__icon" viewBox="0 0 16 16"><path d="M4 1h8v4H4zM1 6h14v6h-2v-2H3v2H1zm3 5h8v4H4z"/></svg>
          907 555 0163
        </li>
        <li class="contact__item">
          <svg class="contact__icon" viewBox="0 0 16 16"><path d="M1 3h14v1.2L8 9 1 4.2zm0 2.6 7 4.8 7-4.8V13H1z"/></svg>
          info@sunwardoilgas.com
        </li>
        <li class="contact__item">
          <svg class="contact__icon" viewBox="0 0 16 16"><path d="M8 1a7 7 0 1 0 0 14A7 7 0 0 0 8 1zm-1 2.2c-.6 1-.4 2 .6 2.3.9.3.6 1.6-.4 1.8-1.2.2-2.3-.6-3.3-.3A5 5 0 0 1 7 3.2zm2.5 9.5c-.3-1.3.6-2.3 1.5-2.8.9-.5 1.3-1.5 1.8-1.8a5 5 0 0 1-3.3 4.6z"/></svg>
          www.sunwardoilgas.com
        </li>
      </ul>
    </div>

    <div class="person">
      <p class="person__name">MARK ELLISON</p>
      <p class="person__title">CEO/FOUNDER</p>
    </div>
  </section>

  <section class="card card--back">
    <div class="back__mark">
      <span class="back__circle"></span>
      <p class="back__name">Sunward Oil &amp; Gas</p>
    </div>
    <p class="back__web">www.sunwardoilgas.com</p>
  </section>
</body>
</html>
```